Meadowlark Property Review is a leading provider of residential appraisal and home inspection products in S

I need a business card/logo designed that obviously describes my business. We are a residential appraisal and home inspection company in Springfield, MO. We offer residential appraisals, home inspection, pest inspection and radon gas measurement. We have been in business for 18 years and hold state certified residential appraisal licenses and OBREX certified home inspection licenses. I have a logo that I really like and will attach, but would be open to new suggestions. I like more modern designs than traditional and would like a two sided card with our services, licenses and qualifications on the back.

```html
<!DOCTYPE html>
<html lang="en">
<head>
<meta charset="utf-8">
<title>Meadowlark Property Review – Business Card</title>
<link rel="stylesheet" href="https://fonts.googleapis.com/css2?family=Lato:wght@400;700;900&display=swap">
<style>
  :root{
    --stage:#2b2b2d;
    --orange:#f29a25;
    --orange-deep:#e8891a;
    --brown:#6b5540;
    --ink:#2e2a26;
    --paper:#f7f7f5;
    --white:#ffffff;
  }
  *{box-sizing:border-box;margin:0;padding:0}
  html,body{width:1200px;height:997px;overflow:hidden;background:var(--stage);font-family:"Lato",sans-serif}
  .canvas{position:relative;width:1200px;height:997px}
  .card{position:absolute;left:270px;width:660px;height:377px;border-radius:3px;box-shadow:0 14px 30px rgba(0,0,0,.45)}
  .card--back{top:70px;background:linear-gradient(135deg,var(--orange) 0%,var(--orange-deep) 100%);color:var(--white)}
  .card--front{top:525px;background:var(--paper);color:var(--ink)}

  /* wordmark: name in one colour and weight, one plain square beside it */
  .wordmark{display:flex;align-items:center;gap:10px;font-weight:900;letter-spacing:.5px;line-height:1.1}
  .wordmark__square{width:14px;height:14px;flex:none}
  .card--back .wordmark{position:absolute;left:48px;top:54px;font-size:24px;color:var(--white);width:260px}
  .card--back .wordmark__square{background:var(--white)}
  .card--front .wordmark{position:absolute;left:0;right:0;top:70px;justify-content:center;font-size:34px;color:var(--brown)}
  .card--front .wordmark__square{background:var(--orange);width:20px;height:20px}

  /* services */
  .services{position:absolute;list-style:none;font-size:17px;line-height:30px}
  .services li{display:flex;align-items:center;gap:12px}
  .services li::before{content:"»";font-weight:900;font-size:20px;opacity:.9}
  .services--left{left:48px;top:160px}
  .services--right{left:360px;top:48px}
  .tagline{position:absolute;left:48px;right:40px;bottom:34px;font-size:16px;letter-spacing:4px;padding-bottom:4px;border-bottom:1.5px solid rgba(255,255,255,.85)}

  /* front */
  .person{position:absolute;right:44px;top:150px;text-align:right}
  .person__name{color:var(--orange);font-weight:900;font-size:22px}
  .person__role{font-size:16px;margin-top:2px}
  .rule{position:absolute;left:44px;top:212px;width:440px;height:2px;background:var(--orange)}
  .contacts{position:absolute;left:44px;top:232px;list-style:none;font-size:17px;line-height:30px}
  .contacts li{display:flex;align-items:center;gap:14px}
  .contacts svg{width:18px;height:18px;fill:var(--brown)}
  .credential{position:absolute;right:44px;top:232px;display:flex;flex-direction:column;align-items:center;gap:10px}
  .credential__seal{width:66px;height:66px;border-radius:50%;background:radial-gradient(circle,#d9b34a 0%,#a77f22 100%);border:3px solid #8c6a1c}
  .credential__years{color:var(--brown);font-size:18px}
</style>
</head>
<body>
<main class="canvas">

  <section class="card card--back" aria-label="Card back – services">
    <div class="wordmark"><span class="wordmark__square"></span>Meadowlark Property Review</div>

    <ul class="services services--right">
      <li>Tax Appeal</li>
      <li>Energy Audits</li>
      <li>Asset Evaluation</li>
      <li>Termite Inspection</li>
      <li>Mechanical Inspection</li>
    </ul>
    <ul class="services services--left">
      <li>Home Inspection</li>
      <li>Pest Inspection</li>
      <li>Residential Appraisals</li>
      <li>Property Inspection</li>
      <li>Radon gas measurement</li>
    </ul>
    <p class="tagline">Delivers Accurate Property Analysis</p>
  </section>

  <section class="card card--front" aria-label="Card front – contact">
    <div class="wordmark"><span class="wordmark__square"></span>Meadowlark Property Review</div>

    <div class="person">
      <p class="person__name">Jordan Ellis</p>
      <p class="person__role">Project Manager/Estimator</p>
    </div>
    <div class="rule"></div>

    <ul class="contacts">
      <li><svg viewBox="0 0 24 24"><path d="M6.6 10.8a15 15 0 0 0 6.6 6.6l2.2-2.2a1 1 0 0 1 1-.25 11.4 11.4 0 0 0 3.6.57 1 1 0 0 1 1 1V20a1 1 0 0 1-1 1A17 17 0 0 1 3 4a1 1 0 0 1 1-1h3.5a1 1 0 0 1 1 1c0 1.25.2 2.45.57 3.6a1 1 0 0 1-.25 1z"/></svg>417-555-0142</li>
      <li><svg viewBox="0 0 24 24"><path d="M6 2h12v6H6zM3 9h18a1 1 0 0 1 1 1v7h-4v5H6v-5H2v-7a1 1 0 0 1 1-1zm5 8v3h8v-3z"/></svg>417-555-0187</li>
      <li><svg viewBox="0 0 24 24"><path d="M2 5h20v14H2zm2 2v.5l8 5 8-5V7z"/></svg>info@meadowlarkreview.com</li>
      <li><svg viewBox="0 0 24 24"><path d="M10 14a4 4 0 0 1 0-5.6l3-3a4 4 0 0 1 5.6 5.6l-1.5 1.5-1.4-1.4 1.5-1.5a2 2 0 0 0-2.8-2.8l-3 3a2 2 0 0 0 0 2.8zm4-4a4 4 0 0 1 0 5.6l-3 3a4 4 0 0 1-5.6-5.6l1.5-1.5 1.4 1.4-1.5 1.5a2 2 0 0 0 2.8 2.8l3-3a2 2 0 0 0 0-2.8z"/></svg>www.meadowlarkreview.com</li>
    </ul>

    <div class="credential">
      <div class="credential__seal" role="img" aria-label="OBREX certification seal"></div>
      <p class="credential__years">18 years Experience</p>
    </div>
  </section>

</main>
</body>
</html>
```